New Baby product needs fun and creative design

We are about to launch are new product for babies and we need some amazing packaging, the product is a snot sucker for blocked noses also known as a nasal aspirator, We are looking for a Creative with a Capital C packaging, we want a nice concept on the box an illustration of a baby and mum using the product like pic attached (example 1) or maybe an illustration of a baby with the pipe, the design has to be new and up to date, I am looking for an animated type feel. Something that make it look baby friendly and comfortable

The packaging is a rectangular box

The colours should be matched with the logo(Baby PIXU) but if not it is still fine as long as there is not a big contrast

Full text for the box will be provided for back and front, the main design will be for the front of the box

Target Market(s)

Mum's with new born babies

Industry/Entity Type

Baby

Requirements
Must have
• Illustration of showing a mum and baby like the example 1
Nice to have
• An animated illustration of a mother and baby using the product or a baby with the pipe in it's nose, something that would look friendly and welcoming for mums
Should not have
• solid colours and medicine like aligned instructional text on the front. Old style designs, should be in line with current designs similar to picture shown

```html
<!DOCTYPE html>
<html lang="en">
<head>
<meta charset="utf-8">
<title>Baby PIXU Nasal Aspirator – Box Front and Side</title>
<link rel="stylesheet" href="https://fonts.googleapis.com/css2?family=Chewy&family=Satisfy&family=Roboto+Condensed:wght@400;700&display=swap">
<style>
  :root {
    --stage-top: #6f8fb8;
    --stage-bottom: #b7c8df;
    --panel-light: #ffffff;
    --panel-shade: #e4e8ee;
    --side-shade: #d9dee6;
    --title-blue: #1ca3e4;
    --title-depth: #0d6fa8;
    --body-blue: #1d8fd0;
    --ink: #4a4a52;
    --brand-pink: #d15aa6;
    --brand-purple: #5b4aa3;
    --tagline-blue: #3b79c8;
    --tagline-rose: #d06a7a;
    --line-violet: #6a6fc0;
    --art-violet: #8a8fd6;
    --warm-glow: #f6b98a;
    --square-grey: #9aa1aa;
    --bullet-orange: #f0a030;
  }
  * { box-sizing: border-box; margin: 0; padding: 0; }
  html, body { width: 1200px; height: 1200px; overflow: hidden; }
  body {
    background: linear-gradient(180deg, var(--stage-top), var(--stage-bottom));
    font-family: "Roboto Condensed", sans-serif;
    position: relative;
  }
  .box-net {
    position: absolute;
    left: 160px; top: 110px;
    width: 880px; height: 980px;
    display: flex;
    box-shadow: 0 20px 50px rgba(40, 60, 90, 0.35);
  }
  .side-panel {
    width: 250px; height: 100%;
    background: linear-gradient(180deg, var(--panel-light) 0%, var(--side-shade) 100%);
    padding: 50px 26px 0;
    position: relative;
    border-right: 1px solid #c9ced6;
  }
  .front-panel {
    width: 630px; height: 100%;
    background: linear-gradient(180deg, var(--panel-light) 0%, var(--panel-light) 45%, var(--panel-shade) 100%);
    position: relative;
    overflow: hidden;
  }
  .brand {
    display: flex; align-items: center; gap: 10px;
    font-family: "Satisfy", cursive;
    color: var(--brand-pink);
  }
  .brand-dot {
    width: 18px; height: 18px; border-radius: 50%;
    background: var(--brand-purple);
  }
  .side-panel .brand { font-size: 30px; justify-content: center; }
  .side-heading {
    font-size: 19px; color: var(--body-blue); font-weight: 700;
    margin-top: 56px; margin-bottom: 10px;
  }
  .contents-list { list-style: none; }
  .contents-list li {
    font-size: 18px; color: var(--ink); line-height: 1.6;
    display: flex; align-items: center; gap: 9px;
  }
  .contents-list li::before {
    content: ""; width: 8px; height: 8px; background: var(--bullet-orange);
  }
  .side-copy { font-size: 18px; color: var(--ink); line-height: 1.55; }
  .front-panel .brand {
    position: absolute; top: 46px; left: 0; right: 0;
    justify-content: center; font-size: 50px;
  }
  .product-title {
    position: absolute; top: 150px; left: 0; right: 0;
    text-align: center;
    font-family: "Chewy", cursive;
    font-size: 96px; font-weight: 400; color: var(--title-blue);
    transform: rotate(-4deg);
    letter-spacing: 1px;
    text-shadow: 0 3px 0 var(--title-depth);
  }
  .product-title .small { font-size: 74px; }
  .mother-baby-art {
    position: absolute; left: 150px; top: 290px;
    width: 460px; height: 520px;
  }
  .tagline-art { position: absolute; left: 0; top: 0; width: 630px; height: 980px; }
  .tagline { font-family: "Satisfy", cursive; font-size: 32px; }
  .tagline .rose { fill: var(--tagline-rose); }
  .square-band { position: absolute; left: 0; right: 0; bottom: 38px; height: 56px; }
</style>
</head>
<body>
  <div class="box-net">
    <section class="side-panel">
      <div class="brand"><span class="brand-dot"></span>Baby PIXU</div>

      <h2 class="side-heading">This box Contains:</h2>
      <ul class="contents-list">
        <li>Suction Pipe</li>
        <li>Replaceable Heads</li>
        <li>Sanitary Box</li>
      </ul>

      <h2 class="side-heading" style="margin-top:34px">Directions for Use</h2>
      <p class="side-copy">Gently position the end of the tubing into the edge of baby's nostril. Using the mouth piece attached, gently suction mucus out of baby's nostril and into the nozzle.<br>After Use: Rinse aspirator with warm soapy water and return to sanitary box ready for the next use.</p>

      <h2 class="side-heading" style="margin-top:26px">Please note:</h2>
      <p class="side-copy">Once opened, remove inner white plastic from the sanitary box.</p>

      <svg class="square-band" viewBox="0 0 250 56" preserveAspectRatio="none" role="img" aria-label="Band of small grey squares">
        <rect x="0" y="0" width="250" height="56" fill="var(--square-grey)" opacity="0.45"/>
      </svg>
    </section>

    <section class="front-panel">
      <div class="brand"><span class="brand-dot"></span>Baby PIXU</div>

      <h1 class="product-title">Nasal <span class="small">Aspirator</span></h1>

      <svg class="mother-baby-art" viewBox="0 0 460 520" role="img" aria-label="Line illustration of a mother kissing her baby's forehead, baby with hand at chin">
        <defs>
          <linearGradient id="artTone" x1="0" y1="0" x2="0.4" y2="1">
            <stop offset="0" stop-color="var(--art-violet)" stop-opacity="0.45"/>
            <stop offset="0.55" stop-color="#c9c8ea" stop-opacity="0.45"/>
            <stop offset="1" stop-color="var(--warm-glow)" stop-opacity="0.7"/>
          </linearGradient>
        </defs>
        <ellipse cx="250" cy="270" rx="200" ry="235" fill="url(#artTone)"/>
      </svg>

      <svg class="tagline-art" viewBox="0 0 630 980">
        <path d="M 523 409 A 205 205 0 1 0 536 711"
              fill="none" stroke="var(--line-violet)" stroke-width="3" opacity="0.6"/>
        <path id="taglineCurve" d="M 160 470 A 250 250 0 0 0 520 780" fill="none"/>
        <text class="tagline" fill="var(--tagline-blue)">
          <textPath href="#taglineCurve" textLength="600" lengthAdjust="spacingAndGlyphs">Gently clear baby's blocked <tspan class="rose">nose in seconds</tspan></textPath>
        </text>
      </svg>

      <svg class="square-band" viewBox="0 0 630 56" preserveAspectRatio="none" role="img" aria-label="Band of small grey squares">
        <rect x="0" y="0" width="630" height="56" fill="var(--square-grey)" opacity="0.45"/>
      </svg>
    </section>
  </div>
</body>
</html>
```